GJ & DW Fencing Pty Ltd

We already have an existing logo created by Pixel Harbour however we have restructured to a company. We would like someone to add Pty Ltd to our business name please.

Colors

Designer to choose only greyscale colors for use in the design.

```html
<!DOCTYPE html>
<html lang="en">
<head>
<meta charset="utf-8">
<title>GJ &amp; DW Fencing Pty Ltd – Business Card</title>
<link rel="stylesheet" href="https://fonts.googleapis.com/css2?family=Merriweather:wght@700&family=Lato:wght@400&display=swap">
<style>
  :root {
    --bg: #d9d9d9;
    --card: #000000;
    --ink: #ffffff;
    --art-light: #f4f5f5;
    --art-mid: #c9caca;
    --shadow: rgba(0, 0, 0, 0.45);
  }
  * { margin: 0; padding: 0; box-sizing: border-box; }
  html, body { width: 1200px; height: 900px; overflow: hidden; }
  body { background: var(--bg); position: relative; }

  .card {
    position: absolute;
    background: var(--card);
    box-shadow: 3px 4px 8px var(--shadow);
    overflow: hidden;
  }
  .card--front { left: 330px; top: 90px; width: 555px; height: 344px; }
  .card--back  { left: 330px; top: 469px; width: 559px; height: 344px; }

  .card__art {
    position: absolute;
    left: 0; top: 0;
    width: 270px; height: 344px;
    background: linear-gradient(160deg, var(--art-light) 0%, var(--art-light) 55%, var(--art-mid) 100%);
  }

  .card__name {
    position: absolute;
    right: 27px; top: 62px;
    font-family: "Merriweather", Georgia, serif;
    font-weight: 700;
    font-size: 20px;
    letter-spacing: 0.3px;
    color: var(--ink);
  }

  .contact {
    position: absolute;
    right: 27px; top: 221px;
    list-style: none;
    font-family: "Lato", Arial, sans-serif;
    font-size: 16.5px;
    color: var(--ink);
  }
  .contact__item {
    display: flex;
    align-items: center;
    justify-content: flex-end;
    gap: 6px;
    height: 24px;
    margin-bottom: 2px;
  }
  .contact__item--address { margin-top: 12px; }
  .contact__icon { width: 23px; height: 23px; flex: none; }

  .brand {
    position: absolute;
    left: 0; right: 0; top: 120px;
    text-align: center;
    font-family: "Merriweather", Georgia, serif;
    font-weight: 700;
    font-size: 32px;
    line-height: 1.2;
    color: var(--ink);
  }
</style>
</head>
<body>

  <section class="card card--front">
    <div class="card__art" role="img" aria-label="Illustration of a white woolly animal facing the viewer"></div>

    <h1 class="card__name">TOM HARROWBY</h1>

    <ul class="contact">
      <li class="contact__item">
        <span>044 5128390</span>
        <svg class="contact__icon" viewBox="0 0 24 24" aria-hidden="true">
          <circle cx="12" cy="12" r="12" fill="var(--ink)"/>
          <path d="M6 10 Q12 5 18 10 L16.5 11.5 L14.5 10.2 L14.5 9 Q12 8 9.5 9 L9.5 10.2 L7.5 11.5 Z M8 12 L16 12 L17 17 L7 17 Z" fill="var(--card)"/>
          <circle cx="12" cy="14.5" r="1.6" fill="var(--ink)"/>
        </svg>
      </li>
      <li class="contact__item">
        <span>Gjdwfencing@mailbox.com</span>
        <svg class="contact__icon" viewBox="0 0 24 24" aria-hidden="true">
          <circle cx="12" cy="12" r="12" fill="var(--ink)"/>
          <rect x="6" y="8" width="12" height="8.5" fill="var(--card)"/>
          <path d="M6.8 8.8 L12 13 L17.2 8.8" fill="none" stroke="var(--ink)" stroke-width="1.1"/>
        </svg>
      </li>
      <li class="contact__item contact__item--address">
        <span>PO Box 418 Kellow WA 6512</span>
        <svg class="contact__icon" viewBox="0 0 24 24" aria-hidden="true">
          <circle cx="12" cy="12" r="12" fill="var(--ink)"/>
          <path d="M12 19 C8.5 14.5 7.5 12.5 7.5 10.5 A4.5 4.5 0 0 1 16.5 10.5 C16.5 12.5 15.5 14.5 12 19 Z" fill="var(--card)"/>
          <circle cx="12" cy="10.5" r="1.8" fill="var(--ink)"/>
        </svg>
      </li>
    </ul>
  </section>

  <section class="card card--back">
    <p class="brand">GJ &amp; DW Fencing<br>Pty Ltd</p>
  </section>

</body>
</html>
```